BrivoNest Learning App for Children with Dyslexia

Project Description:

We are seeking a talented UI/UX designer to create engaging and intuitive designs for Brivonest, an innovative educational app designed to help children learn letters and words through a multisensory learning approach. The app aims to be particularly helpful for children with dyslexia, providing a supportive and interactive learning environment.

Key App Features & Design Requirements:

Account Creation Screen: Design a welcoming and straightforward sign-up page that allows users to register with their email or continue with Quarnix. The design should be clean, focusing on user-friendliness and accessibility, adhering to our terms of service and privacy policy.

Main Screen Design: The main screen should allocate at least 4/6 of its height to the interactive drawing area. It needs to display word prompts in both correct and scrambled orders and include options to "Show all Words," "Play all words," and a search function. The interface should be vibrant, engaging, and easy to navigate for children.

Profile Section: Create a user-friendly profile page that allows users to edit their profile image, name, username, email, links, and bio. The design should be clean and encourage user engagement.

BrivoTally Page: This section will display the user's learning progress, including rankings, a learning curve, and recently learned words. It should visually represent progress in a motivating and understandable way, suitable for a younger audience.

Visual and Auditory Feedback Implementation: Incorporate elements that support visual and auditory feedback, using dyslexia-friendly formats. This includes choosing appropriate colors, fonts, and auditory cues.

Accessibility and Customization Settings: Designs should include settings for adjusting visual contrast, font size, and the word list to accommodate individual preferences and needs.

Feel free to add more interactions and/or pages.

Design preferences:

Color Scheme: Use a bright, inviting color palette that stimulates learning and engagement without overwhelming the users.
Font Selection: Opt for fonts that are readable and accessible, particularly for users with dyslexia.
Icons and Graphics: Design custom icons and graphics that are cohesive with the app's theme and purpose. Illustrations should be simple, relatable, and supportive of the learning process.

Target Market(s)

Educational

Industry/Entity Type

Educational

Colors
0054AA
0677BA
7BADD7
CADEEF
E8F1F8
0094D4
00A9DD
6FCCEA
C7EBF8
E9F6FB

Requirements
Must have
• Educational app, a writing area, scoring and account management
Nice to have
• Statistics, Ranking Page, Settings and some nice visual features

```html
<!DOCTYPE html>
<html lang="en">
<head>
<meta charset="utf-8">
<title>BrivoNest – App Screens</title>
<link rel="stylesheet" href="https://fonts.googleapis.com/css2?family=Poppins:wght@200;300;400;500;600;700;800&display=swap">
<style>
  :root{
    --navy:#0054AA;
    --blue:#0677BA;
    --sky:#0094D4;
    --cyan:#00A9DD;
    --light:#6FCCEA;
    --pale:#CADEEF;
    --mist:#E8F1F8;
    --white:#FFFFFF;
    --yellow:#F6CF2F;
    --ink:#111111;
    --input:#EEF0EE;
    --ghost:#DCE3EC;
  }
  *{box-sizing:border-box;margin:0;padding:0}
  html,body{width:1200px;height:1026px;overflow:hidden}
  body{
    font-family:"Poppins",sans-serif;
    background:linear-gradient(180deg,#FFFFFF 0%,#FFFFFF 45%,#BFD8EC 70%,#2F8ED0 100%);
    position:relative;
  }
  .backdrop-word{
    position:absolute;left:0;right:0;top:24px;
    text-align:center;white-space:nowrap;
    font-family:"Poppins",sans-serif;font-weight:300;
    font-size:180px;letter-spacing:0;line-height:1;
    color:var(--ghost);
  }
  .screen{
    position:absolute;top:202px;width:342px;height:740px;
    border-radius:38px;overflow:hidden;color:var(--white);
  }
  .screen--signup{left:70px;background:radial-gradient(circle at 50% 55%,#0A7FD0 0%,#0668B8 60%,#0557A8 100%)}
  .screen--draw{left:451px;background:linear-gradient(180deg,#0557AE 0%,#0676C4 45%,#0797DB 100%)}
  .screen--profile{left:810px;background:linear-gradient(180deg,#0557AE 0%,#0A6EC0 50%,#0A8FD4 100%)}
  .rings{position:absolute;inset:0}
  .status{position:absolute;top:14px;left:33px;right:24px;display:flex;justify-content:space-between;align-items:center;font-size:14px;font-weight:400}
  .home-bar{position:absolute;bottom:18px;left:50%;width:128px;height:5px;margin-left:-64px;border-radius:3px;background:var(--white)}
  .abs{position:absolute}
  .center-x{left:0;right:0;text-align:center}

  /* sign-up */
  .brand-title{top:46px;font-size:36px;font-weight:700;letter-spacing:1px;line-height:1.1}
  .brand-tag{top:86px;font-size:15px;font-weight:400}
  .hero-art{top:136px;left:38px;width:262px;height:220px;border-radius:24px;background:radial-gradient(circle at 50% 50%,#F2B567 0%,#E9A04C 30%,#4AA0D8 75%,rgba(6,104,184,0) 100%)}
  .signup-heading{top:385px;font-size:19px;font-weight:700;letter-spacing:.3px}
  .signup-sub{top:414px;font-size:15px;font-weight:400}
  .email-field{top:456px;left:26px;width:287px;height:40px;border-radius:20px;background:var(--input);color:#333;font-size:15px;padding:9px 15px}
  .btn-yellow{background:var(--yellow);color:var(--ink);font-weight:700;display:flex;align-items:center;justify-content:center;border-radius:20px;white-space:nowrap}
  .signup-btn{top:509px;left:26px;width:287px;height:40px;font-size:14px}
  .divider{top:568px;left:0;right:0;display:flex;align-items:center;gap:10px;color:var(--yellow);font-size:15px}
  .divider::before,.divider::after{content:"";flex:1;height:1px;background:rgba(255,255,255,.35)}
  .alt-login{top:603px;left:0;right:0;display:flex;justify-content:center;align-items:center;gap:8px;font-size:15px;font-weight:600}
  .alt-login .dot{width:30px;height:30px;border:3px solid var(--white);border-radius:50%}
  .terms{top:644px;font-size:14px;line-height:23px;padding:0 20px}

  /* drawing */
  .icon-btn{width:26px;height:26px;border-radius:50%;background:var(--white);display:flex;align-items:center;justify-content:center}
  .menu-btn{top:69px;left:16px}
  .points{top:70px;right:24px;display:flex;align-items:center;gap:6px;font-size:14px;font-weight:700}
  .coin{width:20px;height:20px;border-radius:50%;background:#F6C62F;border:2px solid #F9DF72}
  .draw-pad{top:114px;left:17px;width:305px;height:237px;background:var(--white);border-radius:14px}
  .mode-toggle{top:383px;left:33px;width:272px;height:36px;border-radius:18px;background:#0A4E9E;display:flex;align-items:center;padding:3px;font-size:12px;font-weight:700;white-space:nowrap}
  .mode-toggle span{flex:1;text-align:center}
  .mode-toggle .active{background:var(--white);color:var(--navy);border-radius:15px;height:30px;line-height:30px}
  .chip{height:31px;width:85px;border-radius:16px;background:var(--white);color:var(--ink);font-size:12px;font-weight:700;display:flex;align-items:center;justify-content:center}
  .results-btn{top:569px;left:67px;width:205px;height:36px;font-size:13px;border-radius:18px}

  /* profile */
  .back-btn{top:67px;left:11px}
  .page-title{top:68px;left:48px;font-size:15px;font-weight:600}
  .avatar{top:132px;left:130px;width:79px;height:79px;border-radius:50%;background:radial-gradient(circle at 50% 45%,#7A5A45 0%,#4A3A2E 55%,#2F3A30 100%)}
  .edit-avatar{top:222px;font-size:16px;display:flex;justify-content:center;align-items:center;gap:6px}
  .field{left:25px;width:291px;border-radius:14px;background:rgba(255,255,255,.16);font-size:15.5px;font-weight:500;display:flex;align-items:center;justify-content:space-between;gap:6px;padding:0 9px 0 14px;white-space:nowrap}
  .field-row{height:35px}
  .field-text{overflow:hidden;letter-spacing:-.2px}
  .chevron{width:26px;height:26px;border-radius:50%;background:var(--white);display:flex;align-items:center;justify-content:center;flex:none}
  .links-box{top:435px;height:141px;display:block;padding:6px 16px}
  .links-box p{line-height:31px}
  .links-box .indent{padding-left:57px}
  .add-link{display:flex;align-items:center;gap:10px;padding-left:22px}
  .plus{width:26px;height:26px;border-radius:50%;background:var(--white);display:flex;align-items:center;justify-content:center}
  .bio-row .field-text{font-size:15px;letter-spacing:-.35px}
</style>
</head>
<body>
  <div class="backdrop-word" aria-hidden="true">BRIVONEST</div>

  <!-- Sign-up screen -->
  <section class="screen screen--signup">
    <svg class="rings" width="342" height="740" aria-hidden="true">
      <g fill="none" stroke="rgba(255,255,255,.08)" stroke-width="1">
        <circle cx="171" cy="400" r="120"/><circle cx="171" cy="400" r="200"/>
        <circle cx="171" cy="400" r="280"/><circle cx="171" cy="400" r="360"/>
        <circle cx="171" cy="400" r="440"/>
      </g>
    </svg>
    <div class="status"><span>9:30</span><svg width="62" height="12" aria-hidden="true"><g fill="#fff"><rect x="0" y="8" width="2" height="4"/><rect x="4" y="6" width="2" height="6"/><rect x="8" y="3" width="2" height="9"/><rect x="12" y="0" width="2" height="12"/><path d="M19 4a10 10 0 0 1 14 0l-1.5 1.5a8 8 0 0 0-11 0zM22 7a6 6 0 0 1 8 0l-4 4z"/><rect x="38" y="1" width="20" height="10" rx="2" fill="none" stroke="#fff"/><rect x="40" y="3" width="16" height="6"/><rect x="59" y="4" width="2" height="4"/></g></svg></div>
    <h1 class="abs center-x brand-title">BRIVONEST</h1>
    <p class="abs center-x brand-tag">Learn letters and words</p>
    <div class="abs hero-art" role="img" aria-label="Illustration of two children learning with a laptop, surrounded by school symbols"></div>
    <h2 class="abs center-x signup-heading">CREATE AN ACCOUNT</h2>
    <p class="abs center-x signup-sub">Enter your email to sign up for this app</p>
    <div class="abs email-field">email@domain.com</div>
    <div class="abs btn-yellow signup-btn">SIGN UP WITH EMAIL</div>
    <div class="abs divider">or Continue With</div>
    <div class="abs alt-login"><span class="dot"></span><span>Quarnix</span></div>
    <p class="abs center-x terms">By clicking continue, you agree to our and<br>Terms of Service Privacy Policy</p>
    <div class="home-bar"></div>
  </section>

  <!-- Drawing screen -->
  <section class="screen screen--draw">
    <div class="status"><span>9:30</span><svg width="62" height="12" aria-hidden="true"><g fill="#fff"><rect x="0" y="8" width="2" height="4"/><rect x="4" y="6" width="2" height="6"/><rect x="8" y="3" width="2" height="9"/><rect x="12" y="0" width="2" height="12"/><path d="M19 4a10 10 0 0 1 14 0l-1.5 1.5a8 8 0 0 0-11 0zM22 7a6 6 0 0 1 8 0l-4 4z"/><rect x="38" y="1" width="20" height="10" rx="2" fill="none" stroke="#fff"/><rect x="40" y="3" width="16" height="6"/><rect x="59" y="4" width="2" height="4"/></g></svg></div>
    <div class="abs icon-btn menu-btn"><svg width="12" height="10" aria-hidden="true"><g stroke="#0054AA" stroke-width="2"><line x1="0" y1="1" x2="12" y2="1"/><line x1="0" y1="5" x2="12" y2="5"/><line x1="0" y1="9" x2="12" y2="9"/></g></svg></div>
    <div class="abs points"><span class="coin"></span>16 Points</div>
    <div class="abs draw-pad">
      <svg width="305" height="237" aria-hidden="true">
        <path d="M48 116 C70 104 95 120 120 124 C145 128 160 112 180 116 C205 121 230 126 255 118 C265 114 272 108 278 104" fill="none" stroke="#2F9BDD" stroke-width="2"/>
        <g transform="translate(151 102) rotate(40)"><rect x="0" y="0" width="6" height="14" fill="#333"/><path d="M0 14 L3 19 L6 14z" fill="#333"/></g>
      </svg>
    </div>
    <div class="abs mode-toggle"><span>SHOW ALL WORDS</span><span class="active">PLAY ALL WORDS</span></div>
    <div class="abs chip" style="top:452px;left:30px">WORD 1</div>
    <div class="abs chip" style="top:452px;left:128px">WORD 2</div>
    <div class="abs chip" style="top:452px;left:225px">WORD 3</div>
    <div class="abs chip" style="top:498px;left:80px">WORD 4</div>
    <div class="abs chip" style="top:498px;left:177px">.....</div>
    <div class="abs btn-yellow results-btn">SHOW ME THE RESULTS</div>
    <div class="home-bar"></div>
  </section>

  <!-- Profile screen -->
  <section class="screen screen--profile">
    <div class="status"><span>9:30</span><svg width="62" height="12" aria-hidden="true"><g fill="#fff"><rect x="0" y="8" width="2" height="4"/><rect x="4" y="6" width="2" height="6"/><rect x="8" y="3" width="2" height="9"/><rect x="12" y="0" width="2" height="12"/><path d="M19 4a10 10 0 0 1 14 0l-1.5 1.5a8 8 0 0 0-11 0zM22 7a6 6 0 0 1 8 0l-4 4z"/><rect x="38" y="1" width="20" height="10" rx="2" fill="none" stroke="#fff"/><rect x="40" y="3" width="16" height="6"/><rect x="59" y="4" width="2" height="4"/></g></svg></div>
    <div class="abs icon-btn back-btn"><svg width="8" height="10" aria-hidden="true"><path d="M6 1 L2 5 L6 9" fill="none" stroke="#0054AA" stroke-width="1.6"/></svg></div>
    <div class="abs page-title">Profile</div>
    <div class="abs avatar" role="img" aria-label="User profile photo"></div>
    <div class="abs center-x edit-avatar">Edit profile image
      <svg width="14" height="14" aria-hidden="true"><path d="M2 12 L3 9 L10 2 L12 4 L5 11z" fill="#fff"/></svg>
    </div>
    <div class="abs field field-row" style="top:282px"><span class="field-text">Name : Tessa Rowan</span><span class="chevron"><svg width="8" height="10" aria-hidden="true"><path d="M2 1 L6 5 L2 9" fill="none" stroke="#0677BA" stroke-width="1.6"/></svg></span></div>
    <div class="abs field field-row" style="top:332px"><span class="field-text">Username : @username</span><span class="chevron"><svg width="8" height="10" aria-hidden="true"><path d="M2 1 L6 5 L2 9" fill="none" stroke="#0677BA" stroke-width="1.6"/></svg></span></div>
    <div class="abs field field-row" style="top:385px"><span class="field-text">Email : name@domain.com</span><span class="chevron"><svg width="8" height="10" aria-hidden="true"><path d="M2 1 L6 5 L2 9" fill="none" stroke="#0677BA" stroke-width="1.6"/></svg></span></div>
    <div class="abs field links-box">
      <p>Links :&nbsp; pagenook.net</p>
      <p class="indent">linkbay.net</p>
      <p class="indent">yourpage.net</p>
      <p class="add-link"><span class="plus"><svg width="10" height="10" aria-hidden="true"><path d="M5 0v10M0 5h10" stroke="#0677BA" stroke-width="2"/></svg></span>Add link</p>
    </div>
    <div class="abs field field-row bio-row" style="top:595px"><span class="field-text">Bio : A description of this user.</span><span class="chevron"><svg width="8" height="10" aria-hidden="true"><path d="M2 1 L6 5 L2 9" fill="none" stroke="#0677BA" stroke-width="1.6"/></svg></span></div>
    <div class="home-bar"></div>
  </section>
</body>
</html>
```